Larkspur Talent IT Recruiting firm needs a business card design for Recruiters, Sourcers, and Account

We need business cards that allow us to change all contact info, names, titles (Recruiter, Sourcer, Account Manager, Director, CEO, etc) per person since we have three offices, in three cities, Phoenix, Austin, and Las Vegas. We do recruiting and contractors for IT positions (Developers, Architects, Software Engineers, Security Engineers, Help Desk, DBAs, PMs, Scrum Masters, etc.) Our client companies are very diverse from Meridian 100 to silicone Valley type start-ups.

So, while we what hip, techie, and quirky, it still needs to be professional. Primary color we use is blue, with silver as a secondary color.

Target Market(s)

IT, Technology

Industry/Entity Type

Business

Contact Information for Business Card

Company name: Larkspur Talent, Inc.
Website: www.larkspurtalent.example
Logos for Careerloop, Blipster, and Myriada

Name, Title, Office Number, Cell Number, email

Font styles to use
Serif
Sans Serif

Colors
0455a3
d5d5d5

Requirements
Nice to have
• The grey I selected below is not necessary - but, would like silver included. I included a card design (File 3: LTI early trial example.jpg) that I had started on. It's very rough, and not quite what we're looking for, but what we did like is the logo, big, maybe a bit faded, off center, goes out of frame, etc. Still looking for other ideas - you are the pros! But, just an idea of a design element we liked.

```html
<!DOCTYPE html>
<html lang="en">
<head>
<meta charset="utf-8">
<title>Larkspur Talent — Business Card</title>
<link href="https://fonts.googleapis.com/css2?family=Cinzel:wght@400&family=Marcellus&family=Montserrat:wght@400;500;700&display=swap" rel="stylesheet">
<style>
  :root{
    --blue:#1f8ad6;
    --blue-deep:#0455a3;
    --blue-light:#35aee6;
    --silver:#d5d5d5;
    --ink:#2b2b2b;
    --muted:#8a8a8a;
    --card:#f7f7f7;
    --backdrop:#e9ebee;
  }
  *{box-sizing:border-box;margin:0;padding:0}
  html,body{width:1200px;height:900px;overflow:hidden;background:var(--backdrop)}
  .stage{position:relative;width:1200px;height:900px}

  .card{
    position:absolute;width:620px;height:354px;overflow:hidden;
    background:linear-gradient(135deg,#ffffff 0%,var(--card) 60%,#ececec 100%);
    box-shadow:0 14px 30px rgba(0,0,0,.18),0 2px 6px rgba(0,0,0,.12);
  }
  .card--front{left:80px;top:60px}
  .card--back{left:500px;top:482px}

  .card__band{
    position:absolute;left:0;right:0;bottom:0;height:16px;
    background:linear-gradient(90deg,var(--blue-deep),var(--blue-light));
  }

  .brand-disc{
    position:absolute;border-radius:50%;
    background:radial-gradient(circle at 40% 30%,var(--blue-light) 0%,var(--blue) 55%,var(--blue-deep) 100%);
    opacity:.92;
  }
  .card--front .brand-disc{width:340px;height:340px;left:360px;top-180px;top:-180px}
  .card--back .brand-disc{width:320px;height:320px;left:400px;top:-170px}

  .lockup{position:absolute;display:flex;flex-direction:column;gap:14px}
  .card--front .lockup{left:44px;top:196px}
  .card--back .lockup{right:40px;top:198px;align-items:flex-end;gap:12px}

  .lockup__mark{display:flex;align-items:center;gap:10px}
  .lockup__dot{width:26px;height:26px;border-radius:50%;background:var(--blue)}
  .lockup__name{
    font-family:"Marcellus",serif;font-size:30px;letter-spacing:4px;
    color:var(--ink);text-transform:uppercase;line-height:1;white-space:nowrap;
  }
  .card--back .lockup__dot{width:22px;height:22px}
  .card--back .lockup__name{font-size:25px;letter-spacing:3px}
  .lockup__tagline{
    font-family:"Cinzel",serif;font-size:11px;letter-spacing:3px;color:#444;white-space:nowrap;
  }

  .contact{position:absolute;left:40px;top:44px;font-family:"Montserrat",sans-serif}
  .person{display:flex;align-items:center;gap:14px;margin-bottom:22px}
  .person__badge{width:30px;height:30px;border:2px solid var(--blue-deep);border-radius:3px}
  .person__name{font-size:17px;font-weight:500;color:var(--ink);letter-spacing:.5px;line-height:1}
  .person__name strong{color:var(--blue);font-weight:700}
  .person__title{font-size:9px;color:var(--muted);letter-spacing:1.5px;margin-top:3px}

  .contact__list{list-style:none;display:flex;flex-direction:column;gap:8px}
  .contact__item{display:flex;align-items:center;gap:14px}
  .contact__icon{
    width:24px;height:24px;flex:none;border:2px solid var(--blue);border-radius:50%;
    display:flex;align-items:center;justify-content:center;
  }
  .contact__icon svg{width:12px;height:12px;fill:var(--blue-deep)}
  .contact__text{font-size:10px;color:var(--ink);letter-spacing:.6px;line-height:1.3;white-space:nowrap}
  .contact__network{color:var(--muted);margin-right:4px}
</style>
</head>
<body>
<main class="stage">

  <section class="card card--front" aria-label="Business card front">
    <div class="brand-disc" aria-hidden="true"></div>
    <div class="lockup">
      <div class="lockup__mark">
        <span class="lockup__dot" aria-hidden="true"></span>
        <span class="lockup__name">Larkspur Talent</span>
      </div>
      <p class="lockup__tagline">TALENT THAT FITS THE ROLE</p>
    </div>
    <div class="card__band"></div>
  </section>

  <section class="card card--back" aria-label="Business card back">
    <div class="brand-disc" aria-hidden="true"></div>

    <div class="contact">
      <div class="person">
        <span class="person__badge" aria-hidden="true"></span>
        <div>
          <p class="person__name"><strong>MARTIN</strong> HALE</p>
          <p class="person__title">SOFTWARE ENGINEER</p>
        </div>
      </div>
      <ul class="contact__list">
        <li class="contact__item"><span class="contact__icon"></span><span class="contact__text"><span class="contact__network">MYRIADA</span>MARTINHALE</span></li>
        <li class="contact__item"><span class="contact__icon"></span><span class="contact__text"><span class="contact__network">BLIPSTER</span>MARTINHALE</span></li>
        <li class="contact__item"><span class="contact__icon"></span><span class="contact__text"><span class="contact__network">CAREERLOOP</span>MARTINHALE</span></li>
        <li class="contact__item">
          <span class="contact__icon"><svg viewBox="0 0 24 24"><path d="M6.6 10.8a15.2 15.2 0 0 0 6.6 6.6l2.2-2.2a1 1 0 0 1 1-.25 11.4 11.4 0 0 0 3.6.57 1 1 0 0 1 1 1V20a1 1 0 0 1-1 1A17 17 0 0 1 3 4a1 1 0 0 1 1-1h3.5a1 1 0 0 1 1 1c0 1.25.2 2.45.57 3.57a1 1 0 0 1-.25 1z"/></svg></span>
          <span class="contact__text">0461 58 3902716<br>0461 58 3902784</span>
        </li>
        <li class="contact__item">
          <span class="contact__icon"><svg viewBox="0 0 24 24"><path d="M3 4h18v12H3zM5 6v8h14V6zM9 18h6v2H9z"/></svg></span>
          <span class="contact__text">info@larkspurtalent.example<br>www.larkspurtalent.example</span>
        </li>
      </ul>
    </div>

    <div class="lockup">
      <div class="lockup__mark">
        <span class="lockup__dot" aria-hidden="true"></span>
        <span class="lockup__name">Larkspur Talent</span>
      </div>
      <p class="lockup__tagline">TALENT THAT FITS THE ROLE</p>
    </div>
    <div class="card__band"></div>
  </section>

</main>
</body>
</html>
```